Business Card Design Project

I require a business card with the following information on them for various different people;
name
m:
f:
e:
I have a logo already and will attached that. We are in the construction industry. I require something clean and simple but eye catching at the same time. You can use another colour with our logo if you like and you can style the logo as well if you wish. I am open.
Also it needs to be front and back design.
Industry/Entity Type
Construction
Requirements
Must have
- Logo, name, mobile, fax and email address.
Front and back design

```html
<!DOCTYPE html>
<html lang="en">
<head>
<meta charset="utf-8">
<title>Oakline Homes — Business Cards</title>
<link href="https://fonts.googleapis.com/css2?family=Montserrat:wght@400;500&display=swap" rel="stylesheet">
<style>
  :root {
    --canvas: #d6d6d4;
    --card-dark: #1c1a19;
    --card-light: #ffffff;
    --band-dark: #221f1e;
    --green: #4fb82e;
    --green-light: #6cd040;
    --green-deep: #3a9a1f;
    --ink: #2b2b2b;
    --paper-text: #f2f2f2;
  }
  html, body {
    margin: 0;
    padding: 0;
    overflow: hidden;
  }
  body {
    width: 1200px;
    height: 944px;
    background: var(--canvas);
    font-family: "Montserrat", Arial, sans-serif;
    position: relative;
  }
  .card {
    position: absolute;
    width: 600px;
    height: 343px;
    border-radius: 22px;
    overflow: hidden;
    box-shadow: 0 10px 28px rgba(0,0,0,0.28);
  }
  /* Back side */
  .card-back {
    left: 90px;
    top: 80px;
    background: linear-gradient(160deg, #2a2726 0%, var(--card-dark) 60%, #141312 100%);
  }
  .card-back .brand {
    position: absolute;
    left: 0;
    right: 0;
    top: 128px;
    display: flex;
    justify-content: center;
    align-items: center;
    gap: 16px;
  }
  .brand-mark {
    width: 28px;
    height: 28px;
    background: var(--green);
    flex: none;
  }
  .brand-name {
    color: var(--green);
    font-weight: 400;
    letter-spacing: 0.5px;
    white-space: nowrap;
  }
  .card-back .brand-name { font-size: 46px; }
  .card-back .website {
    position: absolute;
    left: 0;
    right: 0;
    top: 222px;
    text-align: center;
    color: var(--paper-text);
    font-size: 17px;
    font-weight: 500;
    letter-spacing: 1.5px;
  }
  /* Front side */
  .card-front {
    left: 510px;
    top: 470px;
    background: var(--card-light);
  }
  .card-front .swoosh {
    position: absolute;
    inset: 0;
  }
  .card-front .brand {
    position: absolute;
    left: 44px;
    top: 64px;
    display: flex;
    align-items: center;
    gap: 10px;
  }
  .card-front .brand-mark { width: 20px; height: 20px; }
  .card-front .brand-name { font-size: 30px; }
  .contact-list {
    position: absolute;
    left: 40px;
    top: 196px;
    margin: 0;
    padding: 0;
    list-style: none;
    color: var(--ink);
    font-size: 17px;
    line-height: 24px;
  }
  .contact-list li {
    display: flex;
    align-items: center;
    gap: 9px;
  }
  .contact-list svg { width: 14px; height: 14px; flex: none; }
  .contact-list .web { font-weight: 500; }
  .person {
    position: absolute;
    right: 20px;
    bottom: 40px;
    width: 200px;
    text-align: center;
    color: #ffffff;
  }
  .person-name {
    font-size: 22px;
    font-weight: 400;
    letter-spacing: 0.5px;
  }
  .person-role {
    font-size: 13px;
    margin-top: 2px;
  }
</style>
</head>
<body>

<section class="card card-back" aria-label="Card back">
  <div class="brand">
    <span class="brand-mark"></span>
    <span class="brand-name">Oakline Homes</span>
  </div>
  <div class="website">www.oaklinehomes.com</div>
</section>

<section class="card card-front" aria-label="Card front">
  <svg class="swoosh" viewBox="0 0 600 343" preserveAspectRatio="none" aria-hidden="true">
    <defs>
      <radialGradient id="greenGlow" cx="72%" cy="45%" r="60%">
        <stop offset="0%" stop-color="var(--green-light)"/>
        <stop offset="70%" stop-color="var(--green)"/>
        <stop offset="100%" stop-color="var(--green-deep)"/>
      </radialGradient>
    </defs>
    <path d="M385,0 C330,100 278,230 292,343 L600,343 L600,0 Z" fill="var(--band-dark)"/>
    <path d="M418,0 C375,110 348,240 372,343 L600,343 L600,0 Z" fill="url(#greenGlow)"/>
  </svg>

  <div class="brand">
    <span class="brand-mark"></span>
    <span class="brand-name">Oakline Homes</span>
  </div>

  <ul class="contact-list">
    <li>
      <svg viewBox="0 0 14 14" aria-hidden="true"><circle cx="7" cy="7" r="6" fill="none" stroke="var(--green)" stroke-width="1.6"/><path d="M4.5,4 L6,4 L6.5,5.5 L5.7,6.3 C6.2,7.3 6.8,7.9 7.7,8.3 L8.5,7.5 L10,8 L10,9.5 C7,9.8 4.2,7 4.5,4 Z" fill="var(--green)"/></svg>
      <span>512-555-0142</span>
    </li>
    <li>
      <svg viewBox="0 0 14 14" aria-hidden="true"><rect x="2" y="4" width="10" height="8" rx="1" fill="var(--green)"/><rect x="4" y="1.5" width="6" height="3" fill="none" stroke="var(--green)" stroke-width="1.3"/></svg>
      <span>512-555-0143</span>
    </li>
    <li>
      <svg viewBox="0 0 14 14" aria-hidden="true"><rect x="1.5" y="3" width="11" height="8" rx="1" fill="var(--green)"/><path d="M1.8,3.5 L7,7.5 L12.2,3.5" fill="none" stroke="#ffffff" stroke-width="1.1"/></svg>
      <span>info@oaklinehomes.com</span>
    </li>
    <li>
      <svg viewBox="0 0 14 14" aria-hidden="true"><circle cx="7" cy="7" r="6" fill="var(--green)"/></svg>
      <span class="web">www.oaklinehomes.com</span>
    </li>
  </ul>

  <div class="person">
    <div class="person-name">Mark Ellison</div>
    <div class="person-role">director</div>
  </div>
</section>

</body>
</html>
```